Classy, Elegant, Simple Business Card Design

Looking to have a classy, simple, and elegant design. Want a top notch designed business card. I really like the look of the new torvane credit card. I also like the design I attached. I am trying to reach 21-29 year old females for booking us for there wedding or event. We offer Disc Jockey Service, Photo Booth Rentals, and Uplighting .

Target Market(s)

21-28 year old females

Contact Information for Business Card

Has to have logo, website, email, and phone number

Font styles to use
Other font styles liked:
• open to font choice, modern, clean
Designer to choose
33a6d7
0791cd
0555a3
ffffff

Requirements
Must have
• Has to have logo, website, email, and phone number
Nice to have
• I really like the design of the new torvane credit card. I also included my logo and some designs I like
Should not have
• clutter or too much info

```html
<!DOCTYPE html>
<html lang="en">
<head>
<meta charset="utf-8">
<title>Bellrise Event Group – Business Card</title>
<link rel="stylesheet" href="https://fonts.googleapis.com/css2?family=Josefin+Sans:wght@400&family=Open+Sans:wght@400;600&family=Roboto:wght@400&display=swap">
<style>
  :root {
    --page-bg: #e9e6e2;
    --band-dark: #1b5089;
    --band-light: #2f6ea8;
    --band-edge: #9fa7ae;
    --card-light: #f6f6f5;
    --card-mid: #e4e4e3;
    --name-blue: #1f5c9e;
    --ink: #2b2b2b;
    --icon: #3d5f84;
    --white: #ffffff;
  }
  * { margin: 0; padding: 0; box-sizing: border-box; }
  html, body {
    width: 1200px;
    height: 1054px;
    overflow: hidden;
    background: var(--page-bg);
  }
  .business-card {
    position: absolute;
    left: 100px;
    top: 224px;
    width: 1000px;
    height: 605px;
    background: linear-gradient(160deg, var(--card-light) 0%, var(--card-mid) 100%);
    box-shadow: 0 14px 40px rgba(0,0,0,0.18);
    overflow: hidden;
  }
  .header-band {
    position: absolute;
    inset: 0;
    width: 1000px;
    height: 605px;
  }
  .brand {
    position: absolute;
    left: 0;
    right: 0;
    top: 128px;
    display: flex;
    justify-content: center;
    align-items: center;
    gap: 18px;
  }
  .brand-dot {
    width: 26px;
    height: 26px;
    border-radius: 50%;
    background: var(--white);
  }
  .brand-name {
    font-family: "Josefin Sans", sans-serif;
    font-weight: 400;
    font-size: 40px;
    letter-spacing: 3px;
    color: var(--white);
    text-transform: uppercase;
    line-height: 1;
    padding-top: 6px;
  }
  .holder {
    position: absolute;
    right: 535px;
    top: 418px;
    text-align: right;
  }
  .holder-name {
    font-family: "Open Sans", sans-serif;
    font-weight: 600;
    font-size: 38px;
    color: var(--name-blue);
    line-height: 1.15;
  }
  .holder-title {
    font-family: "Open Sans", sans-serif;
    font-weight: 400;
    font-size: 23px;
    color: var(--ink);
    line-height: 1.4;
  }
  .contact-list {
    position: absolute;
    left: 518px;
    top: 404px;
    list-style: none;
  }
  .contact-item {
    display: flex;
    align-items: center;
    height: 38px;
    font-family: "Roboto", sans-serif;
    font-size: 24px;
    color: var(--ink);
  }
  .contact-icon {
    width: 22px;
    height: 22px;
    margin-right: 16px;
    flex: none;
  }
</style>
</head>
<body>
  <div class="business-card">
    <svg class="header-band" viewBox="0 0 1000 605" aria-hidden="true">
      <defs>
        <linearGradient id="bandFill" x1="0" y1="0" x2="1" y2="1">
          <stop offset="0" stop-color="var(--band-dark)"/>
          <stop offset="0.6" stop-color="var(--band-light)"/>
          <stop offset="1" stop-color="var(--band-dark)"/>
        </linearGradient>
      </defs>
      <path d="M0 0 H1000 V266 Q500 388 0 266 Z" fill="url(#bandFill)"/>
      <path d="M0 266 Q500 388 1000 266" fill="none" stroke="var(--band-edge)" stroke-width="9"/>
    </svg>

    <div class="brand">
      <span class="brand-dot"></span>
      <span class="brand-name">Bellrise Event Group</span>
    </div>

    <div class="holder">
      <p class="holder-name">Clara Dunmore</p>
      <p class="holder-title">Founder &amp; CEO</p>
    </div>

    <ul class="contact-list">
      <li class="contact-item">
        <svg class="contact-icon" viewBox="0 0 24 24" aria-hidden="true">
          <path d="M3 9 Q12 3 21 9 L19 11 L16 9.5 L16 8 Q12 6.5 8 8 L8 9.5 L5 11 Z" fill="var(--icon)"/>
          <path d="M7 11 H17 L19 20 H5 Z" fill="var(--icon)"/>
          <circle cx="12" cy="15.5" r="2.4" fill="var(--card-light)"/>
        </svg>
        <span>415 4150 4150</span>
      </li>
      <li class="contact-item">
        <svg class="contact-icon" viewBox="0 0 24 24" aria-hidden="true">
          <rect x="2" y="5" width="20" height="14" fill="var(--icon)"/>
          <path d="M2.5 5.5 L12 13 L21.5 5.5" fill="none" stroke="var(--card-light)" stroke-width="1.6"/>
        </svg>
        <span>clara@bellrise.com</span>
      </li>
      <li class="contact-item">
        <svg class="contact-icon" viewBox="0 0 24 24" aria-hidden="true">
          <circle cx="12" cy="12" r="9.5" fill="var(--icon)"/>
          <g fill="none" stroke="var(--card-light)" stroke-width="1.2">
            <ellipse cx="12" cy="12" rx="4" ry="9.5"/>
            <line x1="2.5" y1="12" x2="21.5" y2="12"/>
            <line x1="12" y1="2.5" x2="12" y2="21.5"/>
          </g>
        </svg>
        <span>www.bellrise.com</span>
      </li>
    </ul>
  </div>
</body>
</html>
```